Velmoria-Quillmesh Partial Redesign - Web App

Are you able to apply your creativity to an existing layout? I’m convinced that even just a few touches can make a big difference to add personality and professionalism to a website design, and I’m looking for someone able to use existing ideas and bring them to the next level while keeping inside some given constraints.
The actual job is to improve an existing design concept and to apply it creatively to a landing page, a simple home page, and an older web app (single page website).
To help you start with a clear picture of the current situation and of my requirements, I created a detailed brief with screenshots, live examples, and complete instructions. You can find it attached to this job.
My tastes are inclined towards clean and simple designs. For this project I'm not looking for dazzling novelty, but for very solid craftsmanship. Are the right man - or woman - for the job?
Updates
I wanted to thank everybody who participated in this project. I made a choice, but also other designs were interesting. Hope to work with you another time.
Target Market(s)
Our main target is social media marketers and startuppers
Look and feel
Each slider illustrates characteristics of the customer's brand and the style your logo design should communicate.

```html
<!DOCTYPE html>
<html lang="en">
<head>
<meta charset="utf-8">
<title>Velmoria – Explore hashtags</title>
<link rel="stylesheet" href="https://fonts.googleapis.com/css2?family=Source+Sans+3:ital,wght@0,400;0,600;0,700;1,600&display=swap">
<style>
:root{
  --header:#2d2f38;
  --header-deep:#23252c;
  --teal:#0b8fa5;
  --teal-light:#13a9c0;
  --plum:#6b2d4f;
  --orange:#fba84a;
  --bubble:#c4c4c6;
  --panel:#f2f2f2;
  --line:#dcdcdc;
  --text:#3a3a3a;
  --muted:#666;
  --footer:#2f2f2f;
  --link-blue:#1aa3c9;
  --link-red:#b03a2e;
}
*{box-sizing:border-box;margin:0;padding:0}
html,body{width:1200px;height:1148px;overflow:hidden;background:#fff}
body{font-family:"Source Sans 3",sans-serif;color:var(--text)}
.page{position:relative;width:1150px;height:1100px;transform:scale(1.04348);transform-origin:0 0}
.abs{position:absolute}

.site-header{position:absolute;left:0;top:0;width:1150px;height:118px;background:linear-gradient(var(--header),var(--header-deep))}
.brand{position:absolute;left:88px;top:28px;display:flex;align-items:center;gap:16px}
.brand-dot{width:100px;height:60px;border-radius:50%;border:2px solid #fff}
.brand-name{color:#fff;font-weight:700;font-size:36px;line-height:1}
.brand-tag{color:#fff;font-size:12px;margin-top:4px;margin-left:12px}
.search{position:absolute;left:901px;top:24px;width:165px;height:30px;border-radius:15px;background:#fff;border:1px solid #bbb;font-size:11px;font-style:italic;color:#999;padding:8px 22px}
.search svg{position:absolute;right:14px;top:9px}
.shares{position:absolute;right:84px;top:75px;display:flex;gap:8px}
.share{display:flex;height:18px;font-size:10px;font-weight:700}
.share .btn{background:#e9ecf2;border:1px solid #b9bfcc;padding:1px 6px;border-radius:2px;color:#3b4a6b}
.share .count{background:#fff;border:1px solid #ccc;padding:1px 4px;margin-left:3px;color:#333;border-radius:2px}
.share .btn.alt{background:#f06a35;border-color:#e05a25;color:#fff}

.sheen{position:absolute;left:0;top:118px;width:1150px;height:60px;background:linear-gradient(#eaeaea,#fff)}
.nav-frame{position:absolute;left:86px;top:131px;width:980px;height:56px;background:#e4e4e4;border:1px solid #d4d4d4}
.nav{position:absolute;left:91px;top:137px;width:970px;height:46px;background:linear-gradient(var(--teal-light),var(--teal));display:flex;align-items:center;list-style:none}
.nav li{color:#fff;font-size:13px;font-weight:600;text-transform:uppercase;text-align:center}
.nav .active{background:var(--teal-light);height:46px;line-height:46px;width:186px}
.nav .sep{width:1px;height:16px;background:#fff;opacity:.8}

.banner{position:absolute;left:91px;top:183px;width:970px;height:92px;background:linear-gradient(#f4f4f4,#e6e6e6)}
.headline{position:absolute;left:145px;top:219px;font-size:28px;font-style:italic;font-weight:600;color:var(--plum)}
.counter-label{position:absolute;left:733px;top:194px;font-size:13px;color:#444}
.counter-label b{color:var(--plum);font-weight:400;margin-right:10px}
.counter{position:absolute;left:733px;top:218px;display:flex;align-items:flex-end;gap:2px}
.digit{width:28px;height:42px;background:linear-gradient(#333 50%,#111 50%);color:#fff;font-size:34px;font-weight:700;text-align:center;line-height:42px;border-radius:3px}
.comma{font-size:20px;font-weight:700;color:#222;width:10px;text-align:center}

.tag-title{position:absolute;left:89px;top:297px;font-size:24px;color:var(--plum)}
.variants{position:absolute;left:89px;top:331px;font-size:13px;color:#444}
.graph{position:absolute;left:80px;top:360px}
.graph text{font-family:"Source Sans 3",sans-serif;font-size:17px;fill:#fff;text-anchor:middle;dominant-baseline:middle}
.advanced{position:absolute;left:582px;top:700px;width:144px;height:33px;background:var(--plum);color:#fff;font-size:13px;display:flex;align-items:center;justify-content:center;gap:10px;border-radius:2px}

.infl-title{position:absolute;left:746px;top:302px;font-size:18px;color:var(--plum)}
.mascot{position:absolute;left:978px;top:298px;width:54px;height:50px;border-radius:50%;background:radial-gradient(#7fd3ef,#3aa9d6)}
.infl-panel{position:absolute;left:741px;top:337px;width:308px;height:400px;background:#fff;border:1px solid var(--line);box-shadow:inset 0 0 8px #eee}
.infl-row{position:absolute;left:27px;display:flex;align-items:flex-start}
.rank{width:85px;height:36px;background:#ececec;display:flex;align-items:center;padding-left:16px;font-size:11px;color:#444;gap:12px}
.avatar{width:28px;height:28px;background:linear-gradient(#8c6b5a,#3d2c28)}
.infl-info{margin-left:14px;margin-top:-1px}
.infl-name{font-size:15px;color:#333}
.infl-role{font-size:12px;color:#666}

.follow{position:absolute;left:86px;top:806px;width:980px;height:117px;background:var(--panel)}
.follow-kicker{position:absolute;left:29px;top:35px;font-size:11px;font-weight:700;color:var(--link-blue)}
.follow-name{position:absolute;left:29px;top:46px;font-size:30px;font-weight:700;color:var(--link-blue)}
.follow-mark{position:absolute;left:172px;top:30px;width:56px;height:56px;border-radius:8px;background:var(--link-blue)}
.follow-divider{position:absolute;left:266px;top:20px;width:1px;height:82px;background:#d6d6d6}
.post-avatar{position:absolute;left:301px;top:34px;width:32px;height:32px;background:linear-gradient(#6cc2de,#3b9cc2);border:2px solid #fff}
.post{position:absolute;left:345px;top:33px;width:612px;font-size:11.5px;line-height:17px;color:#444}
.post .who{color:var(--link-blue)}
.post a{color:var(--link-red)}
.post-meta{position:absolute;left:346px;top:80px;font-size:9.5px;color:#666}

.site-footer{position:absolute;left:0;top:951px;width:1150px;height:149px;background:var(--footer)}
.foot-brand{position:absolute;left:100px;top:38px;display:flex;align-items:center;gap:10px}
.foot-brand .dot{width:64px;height:40px;border-radius:50%;border:2px solid #777}
.foot-brand span{font-size:22px;font-weight:700;color:#8a8a8a}
.socials{position:absolute;left:886px;top:35px;display:flex;gap:8px}
.socials span{width:30px;height:30px;border-radius:50%;background:#fff}
.copy{position:absolute;left:89px;top:102px;font-size:13px;color:#cfcfcf}
.legal{position:absolute;right:84px;top:102px;font-size:13px;color:#cfcfcf}
.legal i{font-style:normal;margin:0 8px;color:#888}
</style>
</head>
<body>
<div class="page">

<header class="site-header">
  <div class="brand">
    <span class="brand-dot"></span>
    <div>
      <div class="brand-name">Velmoria</div>
      <div class="brand-tag">Social Branding Intelligence</div>
    </div>
  </div>
  <div class="search">Search
    <svg width="12" height="12" viewBox="0 0 12 12"><circle cx="5" cy="5" r="3.5" fill="none" stroke="#888" stroke-width="1.5"/><line x1="7.5" y1="7.5" x2="11" y2="11" stroke="#888" stroke-width="1.8"/></svg>
  </div>
  <div class="shares">
    <div class="share"><span class="btn">Like</span><span class="count">3k</span></div>
    <div class="share"><span class="btn">Post</span><span class="count">316</span></div>
    <div class="share"><span class="btn alt">+1</span><span class="count">81</span></div>
    <div class="share"><span class="btn alt">Share</span><span class="count">4.6K</span></div>
  </div>
</header>

<div class="sheen"></div>
<div class="nav-frame"></div>
<ul class="nav">
  <li class="active">Home</li>
  <li class="sep"></li><li style="width:138px">About us</li>
  <li class="sep"></li><li style="width:118px">Blog</li>
  <li class="sep"></li><li style="width:146px">Summary</li>
  <li class="sep"></li><li style="width:158px">Influencers</li>
  <li class="sep"></li><li style="width:146px">Hashtags</li>
</ul>

<section class="banner"></section>
<h1 class="headline">Explore Chirpline hashtags and their relationships</h1>
<p class="counter-label"><b>Hashtags found so far:</b>in 567,419,411 tweets</p>
<div class="counter">
  <span class="digit">0</span><span class="digit">1</span><span class="comma">,</span>
  <span class="digit">1</span><span class="digit">2</span><span class="digit">0</span><span class="comma">,</span>
  <span class="digit">0</span><span class="digit">2</span><span class="digit">9</span>
</div>

<h2 class="tag-title">#hashtags</h2>
<p class="variants">Variants: hashtags:80% Hashtags:14% HASHTAGS:3% HashTags:3% hashTags:0% Popularity: 57.7</p>

<svg class="graph" width="530" height="410" viewBox="80 360 530 410">
  <g stroke="#cfcfcf" stroke-width="1">
    <line x1="352" y1="543" x2="228" y2="410"/><line x1="352" y1="543" x2="381" y2="411"/>
    <line x1="352" y1="543" x2="533" y2="457"/><line x1="352" y1="543" x2="174" y2="518"/>
    <line x1="352" y1="543" x2="502" y2="586"/><line x1="352" y1="543" x2="142" y2="643"/>
    <line x1="352" y1="543" x2="271" y2="697"/><line x1="352" y1="543" x2="392" y2="716"/>
    <line x1="352" y1="543" x2="520" y2="701"/>
  </g>
  <g fill="var(--bubble)">
    <circle cx="228" cy="410" r="40"/><circle cx="381" cy="411" r="47"/>
    <circle cx="533" cy="457" r="62"/><circle cx="174" cy="518" r="45"/>
    <circle cx="502" cy="586" r="41"/><circle cx="142" cy="643" r="54"/>
    <circle cx="271" cy="697" r="41"/><circle cx="392" cy="716" r="39"/>
    <circle cx="520" cy="701" r="40"/>
  </g>
  <circle cx="352" cy="543" r="54" fill="var(--orange)"/>
  <text x="228" y="410">like</text><text x="381" y="412">the</text>
  <text x="533" y="457">people</text><text x="174" y="518">on</text>
  <text x="502" y="586">tweet</text><text x="140" y="639">to</text>
  <text x="271" y="696">you</text><text x="392" y="716">use</text>
  <text x="520" y="701">use</text><text x="352" y="543">hastags</text>
</svg>

<div class="advanced">Advanced mode
  <svg width="10" height="7" viewBox="0 0 10 7"><path d="M0 0h10L5 7z" fill="#fff"/></svg>
</div>

<h3 class="infl-title">The top 6 influencers for #tag</h3>
<aside class="infl-panel">
  <div class="infl-row" style="top:23px"><div class="rank">No.1<span class="avatar" role="img" aria-label="Profile photo"></span></div><div class="infl-info"><div class="infl-name">Marlowfen 3,265,733</div><div class="infl-role">Support</div></div></div>
  <div class="infl-row" style="top:86px"><div class="rank">No.2<span class="avatar" role="img" aria-label="Profile photo"></span></div><div class="infl-info"><div class="infl-name">TKBrask 3,265,733</div><div class="infl-role">Support</div></div></div>
  <div class="infl-row" style="top:148px"><div class="rank">No.3<span class="avatar" role="img" aria-label="Profile photo"></span></div><div class="infl-info"><div class="infl-name">Ivo Renner 3,265,733</div><div class="infl-role">Support</div></div></div>
  <div class="infl-row" style="top:211px"><div class="rank">No.4<span class="avatar" role="img" aria-label="Profile photo"></span></div><div class="infl-info"><div class="infl-name">Quietbram 3,265,733</div><div class="infl-role">Support</div></div></div>
  <div class="infl-row" style="top:273px"><div class="rank">No.5<span class="avatar" role="img" aria-label="Profile photo"></span></div><div class="infl-info"><div class="infl-name">odile 3,265,733</div><div class="infl-role">Support</div></div></div>
  <div class="infl-row" style="top:336px"><div class="rank">No.6<span class="avatar" role="img" aria-label="Profile photo"></span></div><div class="infl-info"><div class="infl-name">Tano_vero 3,265,733</div><div class="infl-role">Support</div></div></div>
</aside>
<div class="mascot" role="img" aria-label="Blue cartoon bird mascot"></div>

<section class="follow">
  <div class="follow-kicker">FOLLOW US ON</div>
  <div class="follow-name">Chirpline</div>
  <div class="follow-mark"></div>
  <div class="follow-divider"></div>
  <div class="post-avatar" role="img" aria-label="Account avatar"></div>
  <p class="post"><span class="who">Itaque earum rerum hic</span> tenetur a sapiente delectus, ut aut reiciendis voluptatibus maiores alias consequatur aut perfer endis doloribus asperiores modi tempora <a>http://www.lorenta.net/ut/labore/4et</a> dolore magnam.</p>
  <p class="post-meta">2 minutes ago · reply · retweet · favorite</p>
</section>

<footer class="site-footer">
  <div class="foot-brand"><span class="dot"></span><span>Velmoria</span></div>
  <div class="socials"><span></span><span></span><span></span><span></span><span></span></div>
  <p class="copy">Copyright © 2012 www.velmoria.com &nbsp; All rights reserved.</p>
  <p class="legal">Terms and conditions<i>|</i>Privacy policy</p>
</footer>

</div>
</body>
</html>
```